Web Design Project

I want customers to be able to book appointments to get their makeup done and make a deposit and also have a gallery where i put my portfolio images, i want it to be very simple yet elegant.

Target Market(s)

Women ranging from 18-40 that want to get their makeup done

Industry/Entity Type

Makeup

Font styles to use
Sans Serif
Decorative

Requirements
Nice to have
• easy scheduling option and option to pay service in full on website.

```html
<!DOCTYPE html>
<html lang="en">
<head>
<meta charset="utf-8">
<title>Clara Noelle – Make Up Artist</title>
<link rel="stylesheet" href="https://fonts.googleapis.com/css2?family=Jost:wght@300;400&family=Questrial&display=swap">
<style>
:root{
  --ink:#1c1c1c;
  --ink-soft:#262626;
  --band:#2b2b2b;
  --paper:#ffffff;
  --text:#2a2a2a;
  --muted:#b5b5b5;
  --light:#e6e6e6;
  --accent:#c0272d;
  --rule:#5a5a5a;
}
*{margin:0;padding:0;box-sizing:border-box}
html,body{width:1200px;height:792px;overflow:hidden;background:var(--paper)}
body{position:relative;font-family:"Jost",sans-serif;color:var(--text)}
.site-header{position:absolute;left:0;top:0;width:1200px;height:113px;background:var(--ink)}
.brand{position:absolute;left:240px;top:32px;width:210px;font-family:"Jost",sans-serif;font-weight:300;font-size:28px;letter-spacing:1px;color:var(--light);line-height:40px;text-transform:uppercase;white-space:nowrap}
.main-nav{position:absolute;left:510px;top:47px;display:flex;list-style:none}
.main-nav li{height:36px;border-left:1px solid var(--rule);text-align:center;font-family:"Questrial",sans-serif;white-space:nowrap}
.main-nav li:first-child{border-left:none}
.main-nav .label{display:block;font-size:11.5px;color:#fff;letter-spacing:.3px;margin-top:2px}
.main-nav .sub{display:block;font-size:8.5px;color:var(--muted);margin-top:9px}
.nav-home{width:66px}.nav-about{width:93px}.nav-portfolio{width:93px}.nav-testimonials{width:108px}.nav-book{width:100px}
.portfolio-strip{position:absolute;left:0;top:113px;width:1200px;height:158px;display:flex}
.portfolio-strip .shot{width:120px;height:158px}
.strip-band{position:absolute;left:0;top:271px;width:1200px;height:14px;background:var(--band)}
.welcome{position:absolute;left:240px;top:304px;width:722px}
.welcome h1{font-family:"Questrial",sans-serif;font-weight:400;font-size:13.5px;letter-spacing:.4px;text-transform:uppercase;color:var(--text)}
.welcome h1 em{font-style:normal;color:var(--accent)}
.welcome p{margin-top:10px;font-size:10.8px;line-height:15.5px}
.welcome ul{margin-top:14px;padding-left:20px;font-size:10.8px;line-height:15.5px}
.site-footer{position:absolute;left:0;top:626px;width:1200px;height:132px;background:var(--ink);color:var(--light);font-size:10px}
.icon{position:absolute}
.hours{position:absolute;left:269px;top:18px;line-height:16px;white-space:nowrap}
.hours span{display:inline-block;width:38px}
.hours span.wide{width:auto}
.cards{position:absolute;left:270px;top:88px;display:flex;gap:2px}
.cards i{display:block;width:30px;height:20px;border-radius:2px}
.address{position:absolute;left:530px;top:16px;width:160px;line-height:17px;font-size:9.5px}
.phone{position:absolute;left:531px;top:72px;font-size:14.5px;color:var(--light);white-space:nowrap}
.social{position:absolute;left:798px;top:22px;display:flex;gap:6px}
.social i{display:block;width:22px;height:22px;background:#f2f2f2}
.stores{position:absolute;left:802px;top:63px;display:flex;gap:4px}
.stores i{display:block;width:76px;height:26px;background:#0c0c0c;border-radius:4px;border:1px solid #333}
.copyright{position:absolute;left:0;top:758px;width:1200px;height:34px;background:var(--ink-soft);text-align:center;line-height:38px;font-size:9.5px;color:var(--muted)}
</style>
</head>
<body>
<header class="site-header">
  <div class="brand">Clara Noelle</div>
  <ul class="main-nav">
    <li class="nav-home"><span class="label">HOME</span><span class="sub">home page</span></li>
    <li class="nav-about"><span class="label">ABOUT US</span><span class="sub">Clara Noelle</span></li>
    <li class="nav-portfolio"><span class="label">PORTFOLIO</span><span class="sub">my work</span></li>
    <li class="nav-testimonials"><span class="label">TESTIMONIALS</span><span class="sub">what client say</span></li>
    <li class="nav-book"><span class="label">BOOK ONLINE</span><span class="sub">book appoiment</span></li>
  </ul>
</header>

<div class="portfolio-strip">
  <div class="shot" role="img" aria-label="Portfolio portrait, dark backdrop" style="background:linear-gradient(160deg,#2a2320,#a07c68 55%,#1a1412)"></div>
  <div class="shot" role="img" aria-label="Portfolio portrait, pale grey backdrop" style="background:linear-gradient(180deg,#d8d4d2,#b89a88 55%,#3a3634)"></div>
  <div class="shot" role="img" aria-label="Portfolio portrait, long brown hair" style="background:linear-gradient(160deg,#3b2a22,#c59a7e 50%,#4a3226)"></div>
  <div class="shot" role="img" aria-label="Portfolio portrait, violet eye makeup" style="background:linear-gradient(170deg,#e6e2e4,#c6a1a0 50%,#2a2222)"></div>
  <div class="shot" role="img" aria-label="Portfolio portrait, natural look with red hair" style="background:linear-gradient(160deg,#8a5a3c,#e2b9a0 50%,#6a3f2a)"></div>
  <div class="shot" role="img" aria-label="Portfolio portrait, red lips and red nails" style="background:linear-gradient(160deg,#1e1a1a,#c08e7e 50%,#2a1e1c)"></div>
  <div class="shot" role="img" aria-label="Portfolio portrait, smoky eye on black" style="background:linear-gradient(160deg,#0c0c0c,#caa393 55%,#141010)"></div>
  <div class="shot" role="img" aria-label="Portfolio portrait, veiled hat and dark nails" style="background:linear-gradient(160deg,#20242a,#d8c0b6 55%,#2a2224)"></div>
  <div class="shot" role="img" aria-label="Portfolio portrait, classic red lip" style="background:linear-gradient(160deg,#1a1616,#c8a08c 50%,#3a2a24)"></div>
  <div class="shot" role="img" aria-label="Portfolio portrait, bronze glow" style="background:linear-gradient(160deg,#4a3a30,#d0a688 50%,#1e1a18)"></div>
</div>
<div class="strip-band"></div>

<main class="welcome">
  <h1>Welcome to Clara Noelle - <em>Make up artist</em></h1>
  <p>Lorem ipsum dolor sit amet, consectetuer adipiscing elit, sed diam nonummy nibh euismod tincidunt ut laoreet dolore magna aliquam erat volutpat. Ut wisi enim ad minim veniam, quis nostrud exerci tation ullamcorper suscipit lobortis nisl ut aliquip ex ea commodo consequat. Duis autem vel eum iriure dolor in hendrerit in vulputate velit esse molestie consequat, vel illum dolore eu feugiat nulla facilisis at vero eros et accumsan et iusto odio dignissim qui blandit praesent luptatum zzril delenit augue duis dolore te feugait nulla facilisi.</p>
  <ul>
    <li>Lorem ipsum dolor sit amet, consectetuer adipiscing elit.</li>
    <li>Aliquam tincidunt mauris eu risus.</li>
    <li>Vestibulum auctor dapibus neque.</li>
    <li>Nunc dignissim risus id metus.</li>
  </ul>
</main>

<footer class="site-footer">
  <svg class="icon" style="left:240px;top:19px" width="16" height="16" viewBox="0 0 16 16"><circle cx="8" cy="8" r="6.5" fill="none" stroke="#8a8a8a" stroke-width="1.5"/><path d="M8 4v4h3" fill="none" stroke="#8a8a8a" stroke-width="1.5"/></svg>
  <div class="hours">
    <div><span class="wide">Mon - Fri </span>: 9:00am to 7:00pm</div>
    <div><span>Sat</span>: 8:00am to 4:00pm</div>
    <div><span>Sun</span>: Closed</div>
  </div>
  <svg class="icon" style="left:241px;top:89px" width="16" height="12" viewBox="0 0 16 12"><rect x="0.5" y="0.5" width="15" height="11" rx="1" fill="none" stroke="#8a8a8a"/><rect x="0.5" y="3" width="15" height="2.5" fill="#8a8a8a"/></svg>
  <div class="cards">
    <i style="background:#eaeaea"></i><i style="background:#e0e0e0"></i><i style="background:#eeeeee"></i>
  </div>
  <svg class="icon" style="left:504px;top:19px" width="12" height="17" viewBox="0 0 12 17"><path d="M6 0a6 6 0 0 0-6 6c0 4.5 6 11 6 11s6-6.5 6-11a6 6 0 0 0-6-6z" fill="#8a8a8a"/><circle cx="6" cy="6" r="2.2" fill="#1c1c1c"/></svg>
  <div class="address">Lorem ipsum dolor sit amet, consectetuer adipiscing elit, sed diam, nonummy nibh euismod tincidunt</div>
  <svg class="icon" style="left:502px;top:75px" width="18" height="12" viewBox="0 0 18 12"><path d="M1 4c0-2 4-3 8-3s8 1 8 3v1.5h-4V4H5v1.5H1z" fill="#8a8a8a"/><rect x="3" y="6" width="12" height="5.5" rx="1" fill="#8a8a8a"/></svg>
  <div class="phone">0123 456 789</div>
  <div class="social"><i></i><i></i><i></i><i></i><i></i><i></i></div>
  <div class="stores"><i></i><i></i></div>
</footer>
<div class="copyright">Copyright © 2014 by Clara Noelle. All rights reserved.</div>
</body>
</html>
```